Radical T-shirt Company Shopify Site

I would like to have a a Shopify site designed (and built) for my new t-shirt company. The company is called Zest Crew and will feature t-shirt designs focused on different characters doing extreme sports. The brand has a mellow and slightly comical feel. We will feature different artists designs as different collections of the brand.
We do not have a logo yet, but we do have some of the sample designs from the artists that we will be featuring on the site. This will give a feel for the branding and style of the site. As far as colors go, I am not sure if a dark theme or light theme will be best. Please use your best judgement for initial designs. Our t-shirt designs are simple and typically line-art style.
It is important to keep in mind that we have several artists that we will feature and that we want to showcase all of them equally until we can understand which will be most popular. Our sites should speak to audiences of all ages. Light, mellow, and slightly comical describe our brand. The site should catch the audiences eye and allow them to see multiple products so they are more likely to buy multiple products.

Expected deliverables:
1. Zest Crew Outfitters website (focused on mobile device viewing)- including landing page, multiple collections, product pages, variable colors and sized for shirts and other products, about page, contact page, cart with upsells, subscription package functionality, mailing list pop-up, chat support widget, promo codes, payment collection via stripe- All features should be tested and functioning properly before launch. The site must also be set up to A/B test different products, variations, and upsells.
2. Zest Nana Website (Focused on mobile site viewing) - Should follow the same branding (with a different logo but in the same coloring and style as the Zest Crew). This should essentially be a copy of the Zest Crew website include landing page, multiple collections, product pages, variable colors and sized for shirts and other products, about page, contact page, cart with upsells, subscription package functionality, mailing list pop-up, chat support widget, promo codes, payment collection via stripe- Again, this is a duplicate of the Zest Crew website, but with a different landing page tuned to Zest Nana gear.
3. Coding and development of these sites - with the input of 20-30 products (images, descriptions, pricing provided)

I will provide:
1. Examples of products to help with branding and design of the site
2. Feedback on the site
3. All product information for addition to the site
4. Shopify and plugin credentials or access as needed
5. Ongoing work if this goes well

Looking forward to seeing everyone's designs!

Target Market(s)

People that would wear shirts with our characters; grandmas, grandpas, moms, dads, kids, pet lovers- pretty much anyone who enjoys a bit of humor and a nice shirt.

Industry/Entity Type

Comical yet high end t-shirts

Coding

Coded - Design and coding required

Font styles to use
Sans Serif

Requirements
Must have
• Mobile device optimized, Collections carousel on landing page, upsells, features, other recent order popups for users viewing the site, mailing list popup, coupon codes
Nice to have
• Elegant yet playful feel, branding that instills trust and a quick buy.

```html
<!DOCTYPE html>
<html lang="en">
<head>
<meta charset="utf-8">
<title>Zest Nana — Home</title>
<link rel="stylesheet" href="https://fonts.googleapis.com/css2?family=Lato:wght@400;700;900&family=Merriweather:wght@700;900&display=swap">
<style>
:root{
  --ink:#111;
  --text:#444;
  --dark-bar:#2e2e2e;
  --brand-blue:#6cb8d6;
  --button-blue:#7cc1dc;
  --about-bg:#e9f7fc;
  --footer-bg:#acd8e8;
  --card-bg:#f4f4f4;
  --line:#dcdcdc;
  --star:#f07c1a;
  --white:#fff;
}
*{box-sizing:border-box;margin:0;padding:0}
html,body{width:1200px;height:3334px;overflow:hidden}
body{position:relative;background:var(--white);font-family:"Lato",sans-serif;color:var(--ink)}
.abs{position:absolute}

/* top bar */
.top-bar{left:0;top:0;width:1200px;height:53px;background:var(--dark-bar);color:var(--white)}
.top-bar .shipping{left:75px;top:17px;font-size:17px;display:flex;align-items:center;gap:14px}
.top-bar .icons{right:75px;top:16px;display:flex;gap:20px}

/* nav */
.main-nav{left:0;top:53px;width:1200px;height:79px;background:var(--white)}
.main-nav a{position:absolute;top:37px;font-size:12.5px;font-weight:700;letter-spacing:.3px;color:var(--ink);text-decoration:none}
.brand-badge{left:532px;top:14px;width:152px;height:152px;border-radius:50%;background:var(--white);z-index:3;display:flex;align-items:center;justify-content:center}
.brand-name{font-family:"Lato",sans-serif;font-weight:900;font-size:26px;color:var(--brand-blue);text-align:center;line-height:1.05}
.cart{left:1050px;top:34px;display:flex;align-items:center;gap:5px;font-size:12px;font-weight:700}
.cart-count{width:17px;height:17px;border-radius:50%;background:var(--brand-blue);color:var(--white);font-size:11px;text-align:center;line-height:17px;margin-top:-12px}

/* hero */
.hero{left:0;top:132px;width:1200px;height:576px;background:linear-gradient(90deg,#d2d2d0 0%,#e4e4e2 45%,#ebebe9 100%)}
.hero-photo{left:0;top:0;width:640px;height:576px;
  background:
    radial-gradient(ellipse 150px 190px at 250px 330px,#fbfbfb 0%,#f4f4f4 70%,rgba(244,244,244,0) 100%),
    radial-gradient(ellipse 120px 170px at 450px 360px,#fafafa 0%,#f2f2f2 70%,rgba(242,242,242,0) 100%),
    radial-gradient(ellipse 70px 70px at 255px 95px,#b8896c 0%,rgba(184,137,108,0) 100%),
    radial-gradient(ellipse 70px 80px at 425px 130px,#d9b27e 0%,rgba(217,178,126,0) 100%),
    linear-gradient(180deg,rgba(0,0,0,0) 78%,#5d7da6 88%,#3f5f88 100%);
}
.hero-title{right:74px;top:160px;text-align:right;font-weight:900;line-height:1}
.hero-title .l1{font-size:50px;letter-spacing:.5px;color:var(--ink)}
.hero-title .l2{font-size:58px;color:var(--brand-blue);margin-top:2px}
.hero-sub{right:74px;top:278px;text-align:right;font-size:20.5px;font-weight:700;line-height:27px;color:#222}
.btn{display:block;background:var(--button-blue);color:var(--white);text-align:center}
.hero-btn{left:954px;top:347px;width:172px;height:53px;line-height:53px;font-size:22px;font-weight:700}
.promo{right:74px;top:477px;text-align:right}
.promo .label{font-size:20px;font-weight:700;color:#222}
.promo .code{font-size:17px;font-weight:700;color:var(--brand-blue);margin-top:8px;margin-right:32px}
.arrow{width:22px;height:40px}

/* collections */
.collection{top:723px;height:421px}
.collection .label{position:absolute;left:18px;bottom:18px;color:var(--white);font-family:"Merriweather",serif;font-weight:700;font-size:31px;line-height:36px;letter-spacing:1px}

.section-head{font-family:"Merriweather",serif;font-weight:700;letter-spacing:2px;text-align:center;color:var(--ink)}
.rule{height:1px;background:var(--line)}

/* products */
.product{top:1312px;width:241px;height:409px;text-align:center}
.product.boxed{border:2px solid #e6e6e6}
.product .shot{position:absolute;left:35px;top:18px;width:171px;height:206px}
.product .stars{position:absolute;left:0;right:0;top:250px;color:var(--star);font-size:16px;letter-spacing:3px}
.product .name{position:absolute;left:0;right:0;top:279px;font-size:18.5px;color:#333}
.product .price{position:absolute;left:0;right:0;top:307px;font-size:19px;font-weight:900}
.product .add{position:absolute;left:54px;top:348px;width:129px;height:33px;line-height:33px;font-family:"Merriweather",serif;font-size:14px;letter-spacing:.5px}
.sale{left:185px;top:6px;width:48px;height:48px;border-radius:50%;background:var(--brand-blue);color:var(--white);font-size:11px;font-weight:700;line-height:48px;text-align:center}

/* about */
.about{left:0;top:1800px;width:1200px;height:536px;background:var(--about-bg)}
.about-title{left:615px;top:76px;font-family:"Merriweather",serif;font-weight:700;font-size:46px;line-height:53px;letter-spacing:2px}
.about-copy{left:615px;top:196px;width:492px;font-size:17px;line-height:27.7px;color:#4a4a4a}
.about-btn{left:615px;top:407px;width:183px;height:47px;line-height:47px;font-family:"Merriweather",serif;font-size:16px;letter-spacing:.5px}

/* blog */
.post{top:2488px;width:330px;height:372px;background:var(--card-bg);text-align:center}
.post .shot{height:206px}
.post h3{margin-top:22px;font-family:"Merriweather",serif;font-weight:700;font-size:24px;letter-spacing:1px;color:var(--brand-blue)}
.post p{margin-top:10px;font-size:15px;line-height:25px;color:#444}
.post .more{display:inline-block;margin-top:6px;font-family:"Merriweather",serif;font-weight:700;font-size:14px;color:#222;text-decoration:underline}

.chat{left:1129px;top:2935px;width:58px;height:58px;border-radius:50%;background:var(--brand-blue);display:flex;align-items:center;justify-content:center;z-index:3}

/* footer */
.footer{left:0;top:2964px;width:1200px;height:370px;background:var(--footer-bg)}
.footer .brand{left:75px;top:90px;width:170px;height:90px;display:flex;align-items:center;gap:10px}
.footer .brand .dot{width:22px;height:22px;border-radius:50%;background:var(--white)}
.footer .brand .brand-name{color:var(--white);font-size:28px;text-align:left}
.copyright{left:75px;top:214px;font-size:13px;line-height:22px;color:#222}
.social{left:72px;top:272px;display:flex;gap:17px}
.social span{width:20px;height:20px;border-radius:50%;background:#222}
.foot-col h4{font-family:"Merriweather",serif;font-weight:700;font-size:20px;letter-spacing:1px;color:#222}
.foot-col ul{list-style:none;margin-top:14px}
.foot-col li{font-size:14px;line-height:34px;color:#222}
.news-input{left:811px;top:94px;width:253px;height:45px;background:var(--white);font-size:13px;color:#555;padding-left:18px;line-height:45px}
.news-btn{left:1064px;top:94px;width:62px;height:45px;background:var(--brand-blue);display:flex;align-items:center;justify-content:center}
.pay{top:246px;width:36px;height:23px;border-radius:3px;background:#2b2b2b}
</style>
</head>
<body>

<div class="abs top-bar">
  <div class="abs shipping">
    <svg width="20" height="16" viewBox="0 0 20 16"><rect x="0" y="2" width="12" height="9" fill="#fff"/><path d="M12 5h4l3 3v3h-7z" fill="#fff"/><circle cx="4" cy="13" r="2.2" fill="#fff"/><circle cx="15" cy="13" r="2.2" fill="#fff"/></svg>
    <span>Free Shipping Over $250</span>
  </div>
  <div class="abs icons">
    <svg width="20" height="20" viewBox="0 0 20 20"><circle cx="8" cy="8" r="6" stroke="#fff" stroke-width="2.5" fill="none"/><path d="M12.5 12.5L18 18" stroke="#fff" stroke-width="3"/></svg>
    <svg width="18" height="20" viewBox="0 0 18 20"><circle cx="9" cy="6" r="5" fill="#fff"/><path d="M1 20c0-6 4-8 8-8s8 2 8 8z" fill="#fff"/></svg>
    <svg width="16" height="20" viewBox="0 0 16 20"><path d="M4 9V6a4 4 0 0 1 8 0v3" stroke="#fff" stroke-width="2.5" fill="none"/><rect x="1" y="9" width="14" height="10" rx="1" fill="#fff"/></svg>
    <svg width="22" height="20" viewBox="0 0 22 20"><path d="M11 19L2 10a5 5 0 0 1 9-6 5 5 0 0 1 9 6z" fill="#fff"/></svg>
  </div>
</div>

<nav class="abs main-nav">
  <a style="left:74px">HOME</a>
  <a style="left:146px">ABOUT US</a>
  <a style="left:244px">COLLECTIONS</a>
  <a style="left:366px">PRODUCTS</a>
  <a style="left:469px">SHOP</a>
  <a style="left:707px">SUBSCRIPTION PACKAGE</a>
  <a style="left:900px">CONTACT US</a>
</nav>
<div class="abs brand-badge"><div class="brand-name">Zest<br>Nana</div></div>
<div class="abs cart">
  <svg width="18" height="16" viewBox="0 0 18 16"><path d="M0 1h3l2 9h10l2-7H5" stroke="#111" stroke-width="2" fill="none"/><circle cx="7" cy="14" r="1.6" fill="#111"/><circle cx="14" cy="14" r="1.6" fill="#111"/></svg>
  <span>CART</span><span class="cart-count">0</span>
</div>

<section class="abs hero">
  <div class="abs hero-photo" role="img" aria-label="Photo of a smiling couple wearing white Zest Nana line-art t-shirts and jeans"></div>
  <svg class="abs arrow" style="left:43px;top:230px" viewBox="0 0 22 40"><path d="M19 3L3 20l16 17" stroke="#333" stroke-width="2.5" fill="none"/></svg>
  <svg class="abs arrow" style="left:1136px;top:264px" viewBox="0 0 22 40"><path d="M3 3l16 17L3 37" stroke="#333" stroke-width="2.5" fill="none"/></svg>
  <div class="abs hero-title"><div class="l1">WELCOME TO</div><div class="l2">ZEST NANA</div></div>
  <div class="abs hero-sub">Vestibulum ante ipsum primis in faucibus<br>orci luctus et ultrices posuere</div>
  <a class="abs btn hero-btn">Shop Now</a>
  <div class="abs promo"><div class="label">Use Promo Code:</div><div class="code">ZEST NANA</div></div>
</section>

<svg class="abs arrow" style="left:38px;top:913px" viewBox="0 0 22 40"><path d="M19 3L3 20l16 17" stroke="#666" stroke-width="2.5" fill="none"/></svg>
<div class="abs collection" style="left:75px;width:321px;background:linear-gradient(90deg,#3fc0b5 0%,#41bcb1 42%,#d9a83a 52%,#e05a2f 62%,#55b5d8 78%,#3aa0c4 100%)" role="img" aria-label="Stack of folded t-shirts in many colours">
  <div class="label">Shop by<br>Colors</div>
</div>
<div class="abs collection" style="left:411px;width:350px;background:radial-gradient(ellipse 120px 220px at 175px 260px,#1a1a1a 0%,#222 60%,rgba(34,34,34,0) 100%),linear-gradient(180deg,#6f6f6f,#3c3c3c)" role="img" aria-label="Man in a black t-shirt">
  <div class="label">Men’s<br>Collections</div>
</div>
<div class="abs collection" style="left:775px;width:351px;background:radial-gradient(ellipse 110px 200px at 180px 250px,#151515 0%,#1c1c1c 60%,rgba(28,28,28,0) 100%),linear-gradient(180deg,#7a6a62,#4a403c)" role="img" aria-label="Woman in a black t-shirt on stone steps">
  <div class="label">Women’s<br>Collections</div>
</div>
<svg class="abs arrow" style="left:1140px;top:913px" viewBox="0 0 22 40"><path d="M3 3l16 17L3 37" stroke="#666" stroke-width="2.5" fill="none"/></svg>

<div class="abs rule" style="left:75px;top:1240px;width:266px"></div>
<h2 class="abs section-head" style="left:341px;top:1205px;width:518px;font-size:46px">Featured Products</h2>
<div class="abs rule" style="left:859px;top:1240px;width:267px"></div>

<svg class="abs arrow" style="left:38px;top:1496px" viewBox="0 0 22 40"><path d="M19 3L3 20l16 17" stroke="#666" stroke-width="2.5" fill="none"/></svg>
<div class="abs product boxed" style="left:75px">
  <svg class="shot" viewBox="0 0 180 200" role="img" aria-label="Blue t-shirt with line-art surfer print"><path d="M58 8L30 16 2 52l28 20 10-10v134h100V62l10 10 28-20-28-36-28-8q-32 22-64 0z" fill="#1f6fce"/></svg>
  <div class="abs sale">SALE</div>
  <div class="stars">★★★★★</div>
  <div class="name">Etiam nec diam</div>
  <div class="price">$39.00</div>
  <a class="btn add">Add To Cart</a>
</div>
<div class="abs product" style="left:342px">
  <svg class="shot" viewBox="0 0 180 200" role="img" aria-label="Black t-shirt with line-art skater print"><path d="M58 8L30 16 2 52l28 20 10-10v134h100V62l10 10 28-20-28-36-28-8q-32 22-64 0z" fill="#1c1c1c"/></svg>
  <div class="stars">★★★★★</div><div class="name">Etiam nec diam</div><div class="price">$39.00</div>
</div>
<div class="abs product" style="left:614px">
  <svg class="shot" viewBox="0 0 180 200" role="img" aria-label="Olive t-shirt with line-art surfer print"><path d="M58 8L30 16 2 52l28 20 10-10v134h100V62l10 10 28-20-28-36-28-8q-32 22-64 0z" fill="#8d8551"/></svg>
  <div class="stars">★★★★★</div><div class="name">Etiam nec diam</div><div class="price">$39.00</div>
</div>
<div class="abs product" style="left:868px">
  <svg class="shot" viewBox="0 0 180 200" role="img" aria-label="Purple t-shirt with line-art skater print"><path d="M58 8L30 16 2 52l28 20 10-10v134h100V62l10 10 28-20-28-36-28-8q-32 22-64 0z" fill="#5e4a9a"/></svg>
  <div class="stars">★★★★★</div><div class="name">Etiam nec diam</div><div class="price">$39.00</div>
</div>
<svg class="abs arrow" style="left:1140px;top:1496px" viewBox="0 0 22 40"><path d="M3 3l16 17L3 37" stroke="#666" stroke-width="2.5" fill="none"/></svg>

<section class="abs about">
  <div class="abs" style="left:75px;top:80px;width:98px;height:100px;background:var(--brand-blue)"></div>
  <svg class="abs" style="left:85px;top:93px" width="478" height="348" viewBox="0 0 478 348" role="img" aria-label="Grey t-shirt with line-art surfing grandma print on black background">
    <rect width="478" height="348" fill="#000"/>
    <path d="M175 22L120 40 55 118l55 40 22-22v198h214V136l22 22 55-40-65-78-55-18q-64 40-128 0z" fill="#a9a9a9"/>
  </svg>
  <h2 class="abs about-title">About<br>Zest Nana</h2>
  <p class="abs about-copy">Lorem ipsum dolor sit amet, consectetur adipiscing elitellentesque rutrum nibh eu nibh porta molestie. Integer elit odio, tincidunt vitae tellus id, laoreet semper purus. Vivamus a tellus eu leo dictum euismod in eu sapien. Suspendisse nec libero tincidunt, aliquet dolor at, pretium erat. Morbi tincidunt erat ac purus commodo interdum. Integer euismod nec dolor ac condiment pellentesque orci nec.</p>
  <a class="abs btn about-btn">Read More</a>
</section>

<h2 class="abs section-head" style="left:0;top:2385px;width:1200px;font-size:46px">Blog Posts</h2>
<article class="abs post" style="left:75px">
  <div class="shot" style="background:radial-gradient(ellipse 110px 90px at 165px 100px,#fafafa 0%,#f0f0f0 70%,rgba(240,240,240,0) 100%),linear-gradient(135deg,#8a7a6a,#d9d9d9 50%,#3f5a85)" role="img" aria-label="White t-shirt flat lay with jeans and scarf"></div>
  <h3>Neque porro quisqu</h3>
  <p>Morbi tincidunt erat ac purus&nbsp; commodo<br>interdum erat vel felis&nbsp; malesuada</p>
  <a class="more">Read More</a>
</article>
<article class="abs post" style="left:435px">
  <div class="shot" style="background:radial-gradient(ellipse 110px 90px at 165px 100px,#fafafa 0%,#f0f0f0 70%,rgba(240,240,240,0) 100%),linear-gradient(135deg,#5a3020,#7a4a30 50%,#4a2818)" role="img" aria-label="White t-shirt flat lay on wooden table"></div>
  <h3>Neque porro quisqu</h3>
  <p>Morbi tincidunt erat ac purus&nbsp; commodo<br>interdum erat vel felis&nbsp; malesuada</p>
  <a class="more">Read More</a>
</article>
<article class="abs post" style="left:795px">
  <div class="shot" style="background:radial-gradient(ellipse 80px 110px at 160px 140px,#1a1a1a 0%,#222 60%,rgba(34,34,34,0) 100%),linear-gradient(90deg,#d8d6d2,#cfcdc9 50%,#5a4a3e)" role="img" aria-label="Woman wearing a black printed t-shirt"></div>
  <h3>Neque porro quisqu</h3>
  <p>Morbi tincidunt erat ac purus&nbsp; commodo<br>interdum erat vel felis&nbsp; malesuada</p>
  <a class="more">Read More</a>
</article>

<div class="abs chat">
  <svg width="32" height="26" viewBox="0 0 32 26"><ellipse cx="12" cy="10" rx="11" ry="8" fill="#fff"/><path d="M5 16l-2 6 7-4z" fill="#fff"/><ellipse cx="22" cy="15" rx="9" ry="7" fill="#fff" stroke="#6cb8d6" stroke-width="1.5"/></svg>
</div>

<footer class="abs footer">
  <div class="abs brand"><span class="dot"></span><span class="brand-name">Zest Nana</span></div>
  <div class="abs copyright">Copyright © 2022 Company Name<br>All Right Reserved</div>
  <div class="abs social"><span></span><span></span><span></span><span></span><span></span></div>

  <div class="abs foot-col" style="left:362px;top:52px">
    <h4>Navigation</h4>
    <ul><li>Home</li><li>About Us</li><li>Collections</li><li>Products</li><li>Shop</li><li>Subscription Package</li><li>Contact Us</li></ul>
  </div>
  <div class="abs foot-col" style="left:584px;top:52px">
    <h4>My Account</h4>
    <ul><li>My Account</li><li>Shipping</li><li>Returns</li><li>Track Order</li></ul>
  </div>
  <div class="abs foot-col" style="left:811px;top:55px"><h4>Newsletter Signup</h4></div>
  <div class="abs news-input">Enter Email Address</div>
  <div class="abs news-btn"><svg width="22" height="20" viewBox="0 0 22 20"><path d="M2 10h16M11 3l7 7-7 7" stroke="#fff" stroke-width="3.5" fill="none"/></svg></div>
  <div class="abs foot-col" style="left:811px;top:190px"><h4>Payment</h4></div>
  <div class="abs pay" style="left:811px"></div>
  <div class="abs pay" style="left:863px"></div>
  <div class="abs pay" style="left:915px"></div>
  <div class="abs pay" style="left:967px"></div>
  <div class="abs pay" style="left:1019px"></div>
</footer>

</body>
</html>
```